Varnel Corporate Website for technological company

We need a modern website to promote our product and services.
You can found the actually website at the address: www.varnel-example.ch

We are a new company for B2B market. We would like do show our high precision and innovation capability.

we need a section were is possible to easily upload "news" and documents for our customers.

Target Market(s)

B2B services in the industry market

Industry/Entity Type

It Company

Coding

Coded - Design and coding required

Number of Pages Required

5+ page

Font styles to use
Other font styles liked:
• We accept propositions

Requirements
Must have
• Easy to maintain
• Presentation of the Varnel company
• Presentation of Varnel services and products
• The customer can download our ducumentation
Nice to have
• Sexy and modern

```html
<!DOCTYPE html>
<html lang="en">
<head>
<meta charset="utf-8">
<title>Varnel Sagl – Intelligent motion</title>
<link href="https://fonts.googleapis.com/css2?family=Open+Sans:wght@400;600;700;800&display=swap" rel="stylesheet">
<style>
:root{
  --gold:#d6c06a;
  --gold-dark:#b09a4d;
  --olive:#bfb27d;
  --ink:#1e1e1e;
  --text:#444;
  --muted:#8a8a8a;
  --light:#f0f0f0;
  --date:#4a4a4a;
  --footer:#2b2b2b;
  --white:#fff;
}
*{box-sizing:border-box;margin:0;padding:0}
html,body{width:696px;height:1200px;overflow:hidden;background:var(--white)}
body{font-family:"Open Sans",Arial,sans-serif;color:var(--text);position:relative}
.abs{position:absolute}

/* header */
.site-header{position:absolute;left:0;top:0;width:696px;height:61px;background:var(--white)}
.brand{position:absolute;left:77px;top:24px;display:flex;align-items:baseline;gap:5px;color:var(--ink)}
.brand-mark{width:15px;height:15px;background:var(--gold-dark);align-self:center}
.brand-name{font-size:21px;font-weight:800;letter-spacing:1px;line-height:1}
.brand-suffix{font-size:10px;font-weight:800}
.lang{position:absolute;top:17px;display:block;width:7px;height:5px}
.lang.fr{left:598px;background:linear-gradient(90deg,#2b4aa0 33%,#fff 33% 66%,#c8323e 66%)}
.lang.en{left:611px;background:#3a4a8a;box-shadow:inset 0 2px 0 #c8323e,inset 0 -2px 0 #c8323e}
.main-nav{position:absolute;top:38px;right:78px;display:flex;gap:18px;font-size:7.5px;color:var(--ink)}
.main-nav .active{color:var(--gold-dark)}

/* hero */
.hero{position:absolute;left:0;top:61px;width:696px;height:255px;overflow:hidden;background:#151515}
.hero-photo{position:absolute;inset:0;
  background:
    radial-gradient(circle at 232px 152px,rgba(150,180,255,.55) 0 10px,rgba(90,120,220,.25) 20px,transparent 34px),
    radial-gradient(circle at 170px 115px,rgba(225,225,225,.7) 0 8px,transparent 30px),
    radial-gradient(ellipse 130px 120px at 440px 175px,rgba(80,80,80,.35),transparent 70%),
    linear-gradient(90deg,#d8d2c4 0,#8d897f 6%,#2e2e2e 16%,#3a3a3a 30%,#262626 45%,#1d1d1d 60%,#141414 100%)}
.hero-tagline{position:absolute;right:78px;top:101px;font-size:18px;font-weight:600;color:var(--gold)}
.hero-btn{position:absolute;left:477px;top:127px;width:141px;height:23px;border-radius:2px;background:linear-gradient(#d8c47a,#b9a458);color:var(--ink);font-size:7.5px;font-weight:600;display:flex;align-items:center;justify-content:center;gap:4px}
.dots{position:absolute;left:323px;top:235px;display:flex;gap:7px}
.dots span{width:7px;height:7px;border:1px solid #ddd;border-radius:50%}
.dots span.on{background:radial-gradient(#ddd 0 40%,transparent 45%)}

/* intro */
.intro{position:absolute;left:77px;top:337px;width:541px;text-align:center;font-size:7.7px;line-height:12px;color:var(--text)}
.intro p+p{margin-top:12px}

/* services */
.services{position:absolute;left:0;top:430px;width:696px;height:362px;background:var(--olive)}
.section-title{font-weight:700;font-size:13.5px;text-align:center}
.services .section-title{position:absolute;left:0;width:696px;top:24px;color:var(--white)}
.service{position:absolute;width:172px;text-align:center}
.service-photo{height:103px;width:172px}
.service-caption{font-size:8.6px;line-height:11px;color:var(--ink);margin-top:9px;padding:0 2px}

/* products */
.products-title{position:absolute;left:77px;top:824px;font-size:13.5px;font-weight:700;color:var(--ink)}
.carousel-btn{position:absolute;top:827px;width:13px;height:12px;border:1px solid #bbb;display:flex;align-items:center;justify-content:center}
.product{position:absolute;top:853px;width:91px;height:81px;border:1px solid #ccc;background:var(--white);text-align:center}
.product-photo{width:56px;height:40px;margin:10px auto 0}
.product-name{font-size:5.8px;color:var(--ink);margin-top:11px}

/* news */
.news{position:absolute;left:0;top:968px;width:696px;height:148px;background:var(--light)}
.news .section-title{position:absolute;left:0;width:696px;top:25px;color:var(--ink)}
.news-card{position:absolute;top:52px;width:166px;height:70px;background:var(--white);display:flex}
.news-date{width:28px;background:var(--date);color:var(--white);text-align:center;padding-top:3px}
.news-date b{display:block;font-size:13px;line-height:15px;font-weight:700}
.news-date small{display:block;font-size:7.5px;font-weight:700;line-height:8px}
.news-body{padding:11px 8px 0 10px;flex:1}
.news-body h3{font-size:7.6px;font-weight:400;line-height:10px;color:var(--ink)}
.news-body p{font-size:5.2px;line-height:8px;color:var(--muted);margin-top:4px}
.news-body p a{color:var(--ink)}

/* footer */
.site-footer{position:absolute;left:0;top:1116px;width:696px;height:84px;background:var(--footer);text-align:center;color:#ccc}
.footer-nav{position:absolute;top:18px;width:696px;font-size:5.8px}
.copyright{position:absolute;top:34px;width:696px;font-size:5.8px}
.social{position:absolute;top:50px;left:321px;display:flex;gap:5px}
.social span{width:15px;height:15px;border-radius:50%}
</style>
</head>
<body>

<header class="site-header">
  <div class="brand"><span class="brand-mark"></span><span class="brand-name">VARNEL</span><span class="brand-suffix">Sagl</span></div>
  <span class="lang fr"></span><span class="lang en"></span>
  <nav class="main-nav">
    <span class="active">Home</span><span>Services</span><span>Products</span><span>Examples</span><span>Download</span><span>Contacts</span>
  </nav>
</header>

<section class="hero">
  <div class="hero-photo" role="img" aria-label="Precision optical inspection machine with cameras and a blue ring light, in front of a dark close-up of a motor stator"></div>
  <div class="hero-tagline">Intelligent motion</div>
  <div class="hero-btn">
    <svg width="8" height="8" viewBox="0 0 8 8"><path d="M4 0v5M2 3l2 2 2-2M1 7h6" stroke="#1e1e1e" stroke-width="1.3" fill="none"/></svg>
    Download Brouchure Varnel (EN)
  </div>
  <div class="dots"><span class="on"></span><span></span><span></span><span></span></div>
</section>

<section class="intro">
  <p>The ever-increasing complexity in modern systems, the search for reliability and performance and the continuous desire to reduce production costs and dimensions of the products require a rigorous integration between the electronic units, software and mechanical systems.</p>
  <p>VARNEL Ltd. designs systems in which electronics, software and mechanics are perfectly integrated to achieve uncompromising performance. VARNEL Ltd. can develop complete solutions or intervene at a later stage of the product development to carry out studies and / or produce units that will be integrated into your processes, machines or products.</p>
</section>

<section class="services">
  <h2 class="section-title">OUR SERVICES</h2>
  <div class="service" style="left:77px;top:52px">
    <div class="service-photo" role="img" aria-label="Two engineers in suits reviewing a tablet in a bright office" style="background:radial-gradient(ellipse 50px 70px at 120px 70px,#26282d,transparent 80%),radial-gradient(ellipse 40px 60px at 75px 75px,#55585e,transparent 80%),linear-gradient(90deg,#f4f5f6,#dfe2e5 40%,#b8bcc1 70%,#8c9096)"></div>
    <div class="service-caption">Simulation and modeling of complete processes</div>
  </div>
  <div class="service" style="left:262px;top:52px">
    <div class="service-photo" role="img" aria-label="Engineer sketching a machine schematic on a white board" style="background:radial-gradient(ellipse 30px 40px at 150px 85px,#dbe2ea,transparent 80%),repeating-linear-gradient(0deg,#fff 0 9px,#ececec 9px 10px),#fff"></div>
    <div class="service-caption">Concept and design of electronic circuits and mechanical units</div>
  </div>
  <div class="service" style="left:446px;top:52px">
    <div class="service-photo" role="img" aria-label="Hands typing code on a laptop" style="background:radial-gradient(ellipse 60px 30px at 120px 90px,#e6e6e6,transparent 80%),linear-gradient(160deg,#e9c13a 0 6%,#1a1a1a 7%,#2a2a2a 45%,#bfc3c7 65%,#e4e6e8)"></div>
    <div class="service-caption">Development of application specific control software</div>
  </div>
  <div class="service" style="left:77px;top:201px">
    <div class="service-photo" role="img" aria-label="Open hard disk drive mechanism" style="background:radial-gradient(circle at 40px 45px,#e8e8e8 0 14px,#9a9a9a 24px,transparent 40px),radial-gradient(ellipse 50px 30px at 70px 90px,#6a4a30,transparent 80%),linear-gradient(135deg,#3a3a3a,#bdbdbd 45%,#d8d8d8 70%,#7a7a7a)"></div>
    <div class="service-caption">Rapid prototyping (electronic cards, mechanisms ...)</div>
  </div>
  <div class="service" style="left:262px;top:201px">
    <div class="service-photo" role="img" aria-label="CNC milling machine cutting an aluminium part" style="background:radial-gradient(ellipse 40px 25px at 70px 80px,#e9ecef,transparent 80%),radial-gradient(ellipse 25px 20px at 140px 30px,#3a7aa8,transparent 80%),linear-gradient(180deg,#6a6e72,#a6abb0 45%,#dcdfe2 75%,#c3c8cc)"></div>
    <div class="service-caption">Small series manufacturing and setup of industrialization processes</div>
  </div>
  <div class="service" style="left:446px;top:201px">
    <div class="service-photo" role="img" aria-label="Customer support operator wearing a headset" style="background:radial-gradient(ellipse 40px 55px at 105px 60px,#b88a5a,transparent 80%),radial-gradient(ellipse 50px 30px at 110px 105px,#d9dde2,transparent 80%),linear-gradient(90deg,#dfe7ee,#c9d3dc 50%,#d5dce3)"></div>
    <div class="service-caption">Customer service, including support and project monitoring</div>
  </div>
</section>

<h2 class="products-title">OUR PRODUCTS</h2>
<span class="carousel-btn" style="left:588px"><svg width="5" height="6" viewBox="0 0 5 6"><path d="M4 0L1 3l3 3" stroke="#888" fill="none"/></svg></span>
<span class="carousel-btn" style="left:605px"><svg width="5" height="6" viewBox="0 0 5 6"><path d="M1 0l3 3-3 3" stroke="#888" fill="none"/></svg></span>

<div class="product" style="left:77px"><div class="product-photo" role="img" aria-label="Fuel pump motor" style="background:radial-gradient(ellipse 22px 12px at 50% 55%,#c9c2b8,#8a7a68 60%,transparent 75%)"></div><div class="product-name">Aenean efficitur</div></div>
<div class="product" style="left:190px"><div class="product-photo" role="img" aria-label="Electronic circuit board" style="background:radial-gradient(ellipse 26px 14px at 50% 55%,#3f7a4a,#2a4a32 60%,transparent 75%)"></div><div class="product-name">Aenean efficitur</div></div>
<div class="product" style="left:302px"><div class="product-photo" role="img" aria-label="Starter motor" style="background:radial-gradient(ellipse 22px 14px at 50% 55%,#e0e0e0,#8a8a8a 60%,transparent 75%)"></div><div class="product-name">Aenean efficitur</div></div>
<div class="product" style="left:415px"><div class="product-photo" role="img" aria-label="Compact processor module" style="background:radial-gradient(ellipse 22px 14px at 50% 55%,#8a8a3a,#3a3a22 60%,transparent 75%)"></div><div class="product-name">Aenean efficitur</div></div>
<div class="product" style="left:528px"><div class="product-photo" role="img" aria-label="Servo motor" style="background:radial-gradient(ellipse 20px 16px at 50% 55%,#5a5a5a,#1e1e1e 60%,transparent 75%)"></div><div class="product-name">Aenean efficitur</div></div>

<section class="news">
  <h2 class="section-title">NEWS</h2>
  <article class="news-card" style="left:77px">
    <div class="news-date"><b>17</b><small>OCT</small></div>
    <div class="news-body"><h3>Proin interdum sit amet nibh in bibendum</h3><p>The Varnel team will be present at the stand A16 of Techmex exhibition in Bern, between 6 and 8 september 2016 <a>Read more</a></p></div>
  </article>
  <article class="news-card" style="left:265px">
    <div class="news-date"><b>17</b><small>OCT</small></div>
    <div class="news-body"><h3>Proin interdum sit amet nibh in bibendum</h3><p>Added new application notes <a>Read more</a></p></div>
  </article>
  <article class="news-card" style="left:452px">
    <div class="news-date"><b>17</b><small>OCT</small></div>
    <div class="news-body"><h3>Proin interdum sit amet nibh in bibendum</h3><p>Added the 'application' page, showing some of the developments of Varnel Ltd.<br><a>Read more</a></p></div>
  </article>
</section>

<footer class="site-footer">
  <div class="footer-nav">Home &nbsp;|&nbsp; Services &nbsp;|&nbsp; Products &nbsp;|&nbsp; Examples &nbsp;|&nbsp; Download &nbsp;|&nbsp; Contacts</div>
  <div class="copyright">Copyright © 2016 &nbsp;VARNEL Ltd. &nbsp;All rights reserved.</div>
  <div class="social"><span style="background:#3b5998"></span><span style="background:#2aa3e0"></span><span style="background:#c8232c"></span></div>
</footer>

</body>
</html>
```